Web Design For Marlow Pool Service

We are working with a company that wants a website for their pool service. Some sites to use for content/competitors and inspiration:
https://sacramento.brightwaterpoolco.example/builder/newbuild/repair/ppc
https://hollowbrookpoolcareplus.example/
https://lakemontpoolservice.example/
https://www.dravenspoolresurfacing.example/pool-renovation-ga/
Thank you for taking the time to consider designing a website for us. We are web developers based in Stockton, CA, USA. Most of our projects go through the same process. Understanding this process may help you win a project with us. We custom-code all of our websites in-house. We don’t have any requirements as to what tools you use for your design, but we prefer Figma files. For any design that we label as four-stars, we send it to the client for review. The client picks the final design they want us to use. Once we complete this process, we will continue to show additional clients all the four-star sites and purchase them later. Your designs will have multiple chances to sell. For better chances of success, we ask that you follow these guidelines.
IMAGES:
If you use any images or icons in the design, we ask that you have a link to the asset so we can purchase the image/icon. Most of the designs we submit do not have the customer’s images on them unless they have some great images. Be creative; show us the feeling you are trying to portray with your image choices. Use any royalty-free site you choose. We subscribe to Adobe and mainly use their images, but we can purchase images outside of Adobe. PLEASE NOTE: we will not submit designs to clients with watermarks on the images.
FONTS:
We ask that you identify the fonts used in the design. This can be done in a message if you want. We typically use Google Fonts and Adobe Fonts.
CONTENT:
We're always open to different content and ideas. We often submit designs with stock images so the client can see our vision. We typically take pictures after the website launch to use their images with our vision. Lorem Ipsum is fine for paragraphs, but we ask that you write the headers in correct English. We want to be able to show the vision and identify the sections of the website.
INSPIRATION:
We typically add a couple of links in the brief of websites we like to help you get started in your design.
REVISIONS:
We do not often ask for revisions of the designs unless we see something in the design that may not appeal to the client. If there are slight changes that we want to make, we do that in the development process.
FEEDBACK:
We rarely give feedback on designs during the design process. We are working on many website projects and do not have the time to provide feedback. We usually respond if your request is well thought out and asks specific questions, but a note asking “feedback, please” usually goes unanswered.
Number of Pages Required
1 page
Look and feel
Each slider illustrates characteristics of the customer's brand and the style your logo design should communicate.

```html
<!DOCTYPE html>
<html lang="en">
<head>
<meta charset="utf-8">
<title>Marlow Pool Service</title>
<link rel="stylesheet" href="https://fonts.googleapis.com/css2?family=Libre+Caslon+Text:wght@400;700&family=Roboto:ital,wght@0,400;0,500;0,700;1,400&family=Kaushan+Script&display=swap">
<style>
:root{
  --blue:#2196f3;
  --blue-deep:#1565c0;
  --navy:#2c4a6e;
  --nav:#3b5272;
  --ink:#1b1b1b;
  --muted:#6b6b6b;
  --sky:#e4f2fd;
  --night:#0b1826;
  --white:#ffffff;
}
*{box-sizing:border-box;margin:0;padding:0}
html,body{width:1200px;height:4118px;overflow:hidden}
body{position:relative;font-family:"Roboto",sans-serif;color:var(--ink);background:var(--white)}
.abs{position:absolute}
.serif{font-family:"Libre Caslon Text",serif;font-weight:700;text-transform:uppercase;letter-spacing:.5px}
.btn{position:absolute;display:flex;align-items:center;justify-content:center;gap:7px;background:var(--blue);color:var(--white);border-radius:30px;font-weight:700;font-size:13px;text-transform:uppercase}
.btn .dot{width:12px;height:12px;border-radius:50%;background:var(--white);display:inline-flex;align-items:center;justify-content:center}
.btn .dot::after{content:"";border-left:4px solid var(--blue);border-top:3px solid transparent;border-bottom:3px solid transparent;margin-left:1px}
.center{text-align:center;left:0;width:1200px}

/* header */
.topbar{left:0;top:0;width:1200px;height:75px;background:var(--white)}
.brand{left:145px;top:28px;font-family:"Libre Caslon Text",serif;font-size:15px;color:var(--blue);display:flex;align-items:center;gap:7px;white-space:nowrap}
.brand i{width:10px;height:10px;border-radius:50%;background:var(--blue)}
.hours{left:350px;top:30px;font-size:16px;display:flex;align-items:center;gap:8px;white-space:nowrap}
.phone-top{left:868px;top:20px;display:flex;align-items:center;gap:10px}
.phone-top .ic{width:36px;height:36px;border-radius:50%;background:var(--blue);display:flex;align-items:center;justify-content:center}
.phone-top small{display:block;font-size:11px;color:var(--muted)}
.phone-top b{font-size:17px}
.nav{left:0;top:75px;width:1200px;height:40px;background:var(--nav)}
.nav span{position:absolute;top:12px;transform:translateX(-50%);color:var(--white);font-size:13px;font-weight:500;text-transform:uppercase;white-space:nowrap}

/* hero */
.hero{left:0;top:115px;width:1200px;height:680px;background:linear-gradient(180deg,#3f5b36 0%,#6b6a4f 30%,#8a8a80 45%,#3aa8d8 62%,#62c6ec 78%,#9fd9ee 100%)}
.hero-text{color:var(--white);text-shadow:0 1px 4px rgba(0,0,0,.35)}

/* about */
.about-photo{left:136px;top:800px;width:416px;height:416px;border-radius:50%;background:radial-gradient(circle,#5cc4ea,#1f8fc4);border:10px solid var(--navy)}
.about p{font-size:13px;line-height:25px;color:var(--muted);width:440px}

/* services */
.svc-card{position:absolute;top:1536px;width:262px;text-align:center}
.svc-photo{width:262px;height:262px;border-radius:50%;border:7px solid var(--navy);margin:0 auto}
.svc-icon{position:absolute;left:96px;top:219px;width:70px;height:70px;border-radius:50%;background:var(--blue);border:4px solid var(--white);display:flex;align-items:center;justify-content:center}
.svc-card h3{margin-top:42px;font-size:17px;font-weight:500}
.svc-card p{margin-top:10px;font-size:13px;line-height:19px;color:var(--muted);padding:0 8px}
.arrow{position:absolute;top:1653px;width:28px;height:28px;border-radius:50%;background:#111;display:flex;align-items:center;justify-content:center}

/* cta */
.cta{left:0;top:2037px;width:1200px;height:363px;background:linear-gradient(180deg,#2e9cf1,#2b97ef)}

/* testimonials */
.quote{position:absolute;top:2565px;width:395px;height:192px;background:var(--white);padding:22px 20px;overflow:hidden}
.quote .stars{color:#f6c31c;font-size:13px;letter-spacing:3px}
.quote p{font-size:11.5px;font-style:italic;line-height:23px;color:#444;margin-top:10px}
.quote .who{margin-top:10px;font-size:13px;font-weight:500;white-space:nowrap}
.quote .who small{font-size:10px;color:var(--muted);font-weight:400}
.quote.faded{opacity:.28;box-shadow:none;border:1px solid #eee}
.quote.faded p{width:380px}

/* gallery */
.ph{position:absolute}

/* footer */
.footer{left:0;top:3640px;width:1200px;height:478px;background:var(--night);color:var(--white)}
.fcol{position:absolute;top:3816px}
.fcol h4{font-size:16px;font-weight:700;text-transform:uppercase;margin-bottom:14px}
.fcol li{list-style:none;font-size:12px;line-height:25.6px}
.social{display:flex;gap:8px;position:absolute;left:186px;top:3892px}
.social i{width:26px;height:26px;border-radius:50%;border:1.5px solid var(--white)}
.contact-row{display:flex;gap:12px;font-size:12px;line-height:18px;margin-bottom:12px}
.contact-row b{display:block;font-size:11px}
</style>
</head>
<body>

<!-- header -->
<header class="abs topbar">
  <div class="abs brand"><i></i>Marlow Pool Service</div>
  <div class="abs hours">
    <svg width="16" height="16" viewBox="0 0 16 16"><circle cx="8" cy="8" r="6.5" fill="none" stroke="#2196f3" stroke-width="1.6"/><path d="M8 4.5V8l2.5 1.5" fill="none" stroke="#2196f3" stroke-width="1.6"/></svg>
    Open 24 Hours at All our Locations!
  </div>
  <div class="btn" style="left:694px;top:22px;width:134px;height:38px;font-weight:500;text-transform:none;font-size:14px">Get A Quote</div>
  <div class="abs phone-top">
    <span class="ic"><svg width="18" height="18" viewBox="0 0 24 24"><path d="M6.6 10.8a15 15 0 006.6 6.6l2.2-2.2c.3-.3.7-.4 1-.2 1.1.4 2.3.6 3.6.6.6 0 1 .4 1 1V20c0 .6-.4 1-1 1A17 17 0 013 4c0-.6.4-1 1-1h3.5c.6 0 1 .4 1 1 0 1.3.2 2.5.6 3.6.1.3 0 .7-.2 1z" fill="#fff"/></svg></span>
    <div><small>Call or Text us</small><b>+1-888-888-8888</b></div>
  </div>
</header>
<nav class="abs nav">
  <span style="left:165px">Home</span>
  <span style="left:287px">About Us</span>
  <span style="left:428px">Services &#8964;</span>
  <span style="left:580px">Installation</span>
  <span style="left:724px">Gallery</span>
  <span style="left:862px">Products &#8964;</span>
  <span style="left:1013px">Contact Us</span>
</nav>

<!-- hero -->
<section class="abs hero" role="img" aria-label="Backyard swimming pool with potted plants, garden trees and wooden fence"></section>
<div class="abs center hero-text" style="top:270px;font-size:14px;font-weight:700">WELCOME TO</div>
<h1 class="abs center hero-text serif" style="top:296px;font-size:36px;font-weight:400">Marlow Pool Service</h1>
<p class="abs center hero-text" style="top:352px;font-size:15px;line-height:24px;font-weight:500">Lorem ipsum dolor sit amet, consectetur adipiscing elit,<br>sed do eiusmod tempor incididunt ut labore.</p>
<div class="btn" style="left:508px;top:426px;width:184px;height:44px;font-size:14px">Get Started <span class="dot"></span></div>
<svg class="abs" style="left:0;top:680px" width="1200" height="120" viewBox="0 0 1200 120">
  <path d="M0 110 C200 20 420 20 640 70 C860 120 1040 100 1200 50 V120 H0Z" fill="#fff"/>
  <path d="M0 106 C200 16 420 16 640 66 C860 116 1040 96 1200 46" fill="none" stroke="#1e8fe6" stroke-width="8"/>
  <path d="M0 96 C210 5 420 10 640 56 C860 104 1040 86 1200 34" fill="none" stroke="#1565c0" stroke-width="3"/>
</svg>

<!-- about -->
<div class="abs about-photo" role="img" aria-label="Family smiling together in a swimming pool"></div>
<section class="about">
  <h2 class="abs serif" style="left:617px;top:848px;font-size:30px">About <span style="color:var(--navy)">Us</span></h2>
  <p class="abs" style="left:617px;top:905px">Lorem ipsum dolor sit amet, consectetur adipiscing elit, sed do eiusmod tempor incididunt ut labore et dolore magna aliqua. Ut enim ad minim veniam, quis nostrud exercitation ullamco laboris nisi ut aliquip ex ea commodo consequat. Duis aute irure dolor in reprehenderit in voluptate velit esse cillum dolore eu fugiat nulla pariatur.</p>
  <p class="abs" style="left:617px;top:1042px">Excepteur sint occaecat cupidatat non proident, sunt in culpa qui officia deserunt mollit anim id est laborum.</p>
  <div class="btn" style="left:617px;top:1121px;width:182px;height:47px">Read More <span class="dot"></span></div>
</section>

<!-- services -->
<svg class="abs" style="left:0;top:1270px" width="1200" height="770" viewBox="0 0 1200 770">
  <path d="M0 50 C150 20 260 110 420 80 C560 55 640 -10 800 20 C960 50 1080 40 1200 30 V770 H0Z" fill="#e4f2fd"/>
</svg>
<h2 class="abs center serif" style="top:1444px;font-size:30px">Expert <span style="color:var(--blue)">Pool</span> Services</h2>
<span class="arrow" style="left:82px"><svg width="10" height="10" viewBox="0 0 10 10"><path d="M7 1L3 5l4 4" fill="none" stroke="#fff" stroke-width="2"/></svg></span>
<span class="arrow" style="left:1090px"><svg width="10" height="10" viewBox="0 0 10 10"><path d="M3 1l4 4-4 4" fill="none" stroke="#fff" stroke-width="2"/></svg></span>

<div class="svc-card" style="left:145px">
  <div class="svc-photo" role="img" aria-label="Swimmer doing laps in a pool" style="background:linear-gradient(160deg,#7fd3f2,#2a9ad6)"></div>
  <span class="svc-icon"><svg width="32" height="32" viewBox="0 0 32 32"><circle cx="22" cy="9" r="3" fill="#fff"/><path d="M5 18l8-6 5 4M3 23c3 0 3-2 6-2s3 2 6 2 3-2 6-2 3 2 6 2" fill="none" stroke="#fff" stroke-width="2.4" stroke-linecap="round"/></svg></span>
  <h3>Swimming Pool Services</h3>
  <p>Lorem ipsum dolor sit amet, consectetur adipiscing elit, sed do eiusmod.</p>
  <div class="btn" style="position:relative;margin:14px auto 0;width:140px;height:35px;font-size:12px">Learn More <span class="dot"></span></div>
</div>
<div class="svc-card" style="left:470px">
  <div class="svc-photo" role="img" aria-label="Technician cleaning a pool with a long pole" style="background:linear-gradient(180deg,#8a9a86 0%,#7c8f7a 45%,#6bb9e0 70%,#3aa0d8)"></div>
  <span class="svc-icon"><svg width="30" height="30" viewBox="0 0 30 30"><path d="M10 4v18M20 4v18M10 9h10M10 14h10M4 24c3 0 3-2 5.5-2s2.5 2 5.5 2 3-2 5.5-2 2.5 2 5.5 2" fill="none" stroke="#fff" stroke-width="2.2" stroke-linecap="round"/></svg></span>
  <h3>Pool Cleaning Services</h3>
  <p>Lorem ipsum dolor sit amet, consectetur adipiscing elit, sed do eiusmod.</p>
  <div class="btn" style="position:relative;margin:14px auto 0;width:140px;height:35px;font-size:12px">Learn More <span class="dot"></span></div>
</div>
<div class="svc-card" style="left:793px">
  <div class="svc-photo" role="img" aria-label="Worker repairing pool edge tiles" style="background:linear-gradient(180deg,#6f8c5c 0%,#8fa377 40%,#c9c2b2 60%,#4ab2e2)"></div>
  <span class="svc-icon"><svg width="30" height="30" viewBox="0 0 30 30"><circle cx="15" cy="11" r="6" fill="none" stroke="#fff" stroke-width="2.2"/><path d="M5 27c0-6 4-9 10-9s10 3 10 9" fill="none" stroke="#fff" stroke-width="2.2"/></svg></span>
  <h3>Swimming Pool Repairs</h3>
  <p>Lorem ipsum dolor sit amet, consectetur adipiscing elit, sed do eiusmod.</p>
  <div class="btn" style="position:relative;margin:14px auto 0;width:140px;height:35px;font-size:12px">Learn More <span class="dot"></span></div>
</div>

<!-- call to action -->
<section class="abs cta"></section>
<h2 class="abs center serif" style="top:2094px;font-size:29px;color:var(--white)">Speak with one of our experts today!</h2>
<p class="abs center" style="top:2158px;font-size:16px;line-height:28px;color:var(--white)">Lorem ipsum dolor sit amet, consectetur adipiscing elit, sed do eiusmod tempor incididunt ut labore et dolore<br>Ut enim ad minim veniam, quis nostrud exercitation ullamco laboris nisi ut aliquip.</p>
<span class="abs" style="left:238px;top:2280px;width:40px;height:40px;border-radius:50%;background:var(--white);display:flex;align-items:center;justify-content:center"><svg width="20" height="20" viewBox="0 0 24 24"><path d="M6.6 10.8a15 15 0 006.6 6.6l2.2-2.2c.3-.3.7-.4 1-.2 1.1.4 2.3.6 3.6.6.6 0 1 .4 1 1V20c0 .6-.4 1-1 1A17 17 0 013 4c0-.6.4-1 1-1h3.5c.6 0 1 .4 1 1 0 1.3.2 2.5.6 3.6.1.3 0 .7-.2 1z" fill="#2196f3"/></svg></span>
<div class="abs" style="left:292px;top:2268px;color:var(--white);font-size:16px;font-weight:500">Need help now?</div>
<div class="abs" style="left:291px;top:2292px;color:var(--white);font-size:31px;font-weight:500;white-space:nowrap">Call: +1-888-888-8888</div>
<svg class="abs" style="left:628px;top:2252px" width="115" height="24" viewBox="0 0 115 24"><path d="M2 20C30 4 70 2 110 14" fill="none" stroke="#fff" stroke-width="1.6"/><path d="M102 8l9 6-10 3" fill="none" stroke="#fff" stroke-width="1.6"/></svg>
<div class="abs" style="left:666px;top:2276px;color:var(--white);font-family:'Kaushan Script',cursive;font-size:28px">or</div>
<div class="btn" style="left:767px;top:2282px;width:194px;height:56px;background:var(--white);color:var(--blue);font-size:16px">Contact Us <span class="dot" style="background:var(--blue)"></span></div>

<!-- testimonials -->
<h2 class="abs center serif" style="top:2483px;font-size:30px">What our <span style="color:var(--navy)">Clients</span> Say</h2>
<div class="quote faded" style="left:144px;width:257px">
  <div class="stars">★★★★★</div>
  <p>Lorem ipsum dolor sit amet, consectetur adipiscing elit, sed do eiusmod tempor incididunt ut labore et dolore magna aliqua. Ut enim ad minim veniam, quis nostrud exercitation ullamco laboris nisi ut aliquip ex ea commodo consequat.</p>
  <div class="who">Jhone Duo - <small>Sed ut perspiciatis unde</small></div>
</div>
<div class="quote faded" style="left:796px;width:259px;padding-left:0">
  <p style="margin-top:33px;margin-left:-130px">Lorem ipsum dolor sit amet, consectetur adipiscing elit, sed do eiusmod tempor incididunt ut labore et dolore magna aliqua. Ut enim ad minim veniam, quis nostrud exercitation ullamco laboris nisi ut aliquip ex ea commodo consequat.</p>
</div>
<div class="quote" style="left:401px;box-shadow:0 4px 18px rgba(0,0,0,.15)">
  <div class="stars">★★★★★</div>
  <p>Lorem ipsum dolor sit amet, consectetur adipiscing elit, sed do eiusmod tempor incididunt ut labore et dolore magna aliqua. Ut enim ad minim veniam, quis nostrud exercitation ullamco laboris nisi ut aliquip ex ea commodo consequat.</p>
  <div class="who">Jhone Duo - <small>Sed ut perspiciatis unde</small></div>
  <svg class="abs" style="right:14px;bottom:12px" width="46" height="36" viewBox="0 0 46 36"><path d="M2 34V20C2 10 8 3 18 2v6c-5 1-8 5-8 10h8v16zM26 34V20c0-10 6-17 16-18v6c-5 1-8 5-8 10h8v16z" fill="#e6e6e6"/></svg>
</div>
<div class="abs" style="left:577px;top:2798px;display:flex;gap:5px">
  <i style="width:11px;height:11px;border-radius:50%;border:2px solid #222"></i>
  <i style="width:11px;height:11px;border-radius:50%;border:2px solid #222;background:radial-gradient(#222 35%,transparent 40%)"></i>
  <i style="width:11px;height:11px;border-radius:50%;border:2px solid #222"></i>
</div>

<!-- gallery -->
<h2 class="abs center serif" style="top:2886px;font-size:30px;color:var(--navy)">Our <span style="color:var(--ink)">Gallery</span></h2>
<div class="ph" role="img" aria-label="Children swimming underwater with goggles" style="left:144px;top:2967px;width:450px;height:261px;background:linear-gradient(160deg,#5cc3ea,#1d7fc7)"></div>
<div class="ph" role="img" aria-label="Friends jumping into a pool outdoors" style="left:604px;top:2967px;width:451px;height:261px;background:linear-gradient(180deg,#b9d3e6 0%,#5f8a4f 55%,#4fb6d6 100%)"></div>
<div class="ph" role="img" aria-label="Pool party with inflatable flamingo" style="left:144px;top:3239px;width:299px;height:233px;background:linear-gradient(180deg,#d8ecf6 0%,#7da860 45%,#3fb4e2 100%)"></div>
<div class="ph" role="img" aria-label="Group of friends relaxing on floats in a pool" style="left:454px;top:3239px;width:289px;height:233px;background:linear-gradient(170deg,#c9a88a,#4cb8e4)"></div>
<div class="ph" role="img" aria-label="Couple in sunglasses enjoying the pool" style="left:753px;top:3239px;width:300px;height:233px;background:linear-gradient(150deg,#2aa8e4,#b98c6a 60%,#3ab0e4)"></div>
<div class="btn" style="left:527px;top:3524px;width:147px;height:46px">View More <span class="dot"></span></div>

<!-- footer -->
<section class="abs footer" role="img" aria-label="Dark water texture"></section>
<svg class="abs" style="left:0;top:3600px" width="1200" height="80" viewBox="0 0 1200 80">
  <path d="M0 40 C200 -5 420 10 620 45 C820 78 1020 60 1200 10 V80 H0Z" fill="#0b1826"/>
  <path d="M0 44 C200 0 420 14 620 48 C820 80 1020 62 1200 14" fill="none" stroke="#1e8fe6" stroke-width="8"/>
  <path d="M0 30 C200 -10 420 6 620 36 C820 66 1020 50 1200 2" fill="none" stroke="#1565c0" stroke-width="3"/>
</svg>
<div class="abs" style="left:146px;top:3852px;color:var(--blue);font-family:'Libre Caslon Text',serif;font-size:21px;display:flex;align-items:center;gap:8px;white-space:nowrap"><i style="width:12px;height:12px;background:var(--blue);border-radius:50%"></i>Marlow Pool Service</div>
<div class="social"><i></i><i></i><i></i><i></i><i></i></div>
<div class="fcol" style="left:435px;color:var(--white)">
  <h4>Qucik Links</h4>
  <ul><li>Home</li><li>About Us</li><li>Services</li><li>Installation</li><li>Gallery</li><li>Products</li><li>Contact Us</li></ul>
</div>
<div class="fcol" style="left:626px;color:var(--white)">
  <h4>About Company</h4>
  <ul><li>Terms of Use</li><li>Terms &amp; Condition</li><li>News</li><li>Privacy Policy</li><li>FAQ</li></ul>
</div>
<div class="fcol" style="left:868px;color:var(--white)">
  <h4>Contact Us</h4>
  <div class="contact-row"><svg width="12" height="12" viewBox="0 0 24 24"><path d="M6.6 10.8a15 15 0 006.6 6.6l2.2-2.2c.3-.3.7-.4 1-.2 1.1.4 2.3.6 3.6.6.6 0 1 .4 1 1V20c0 .6-.4 1-1 1A17 17 0 013 4c0-.6.4-1 1-1h3.5c.6 0 1 .4 1 1 0 1.3.2 2.5.6 3.6.1.3 0 .7-.2 1z" fill="#2196f3"/></svg><div><b>Phone</b>+1-888-888-8888</div></div>
  <div class="contact-row"><svg width="14" height="12" viewBox="0 0 14 12"><rect width="14" height="11" rx="1.5" fill="#2196f3"/><path d="M1 1.5l6 4.5 6-4.5" fill="none" stroke="#0b1826" stroke-width="1.3"/></svg><div><b>Email</b>info@marlowpoolservice.com</div></div>
  <div class="contact-row"><svg width="12" height="14" viewBox="0 0 12 14"><path d="M6 14S1 8 1 5a5 5 0 0110 0c0 3-5 9-5 9z" fill="#2196f3"/><circle cx="6" cy="5" r="1.8" fill="#0b1826"/></svg><div><b>Location</b>Lorem ipsum dolor sit amet,<br>consectetur&nbsp; 6514</div></div>
</div>
<span class="abs" style="left:1080px;top:4032px;width:32px;height:32px;border-radius:50%;background:var(--blue)"></span>
<div class="abs" style="left:144px;top:4051px;width:912px;height:1px;background:rgba(255,255,255,.25)"></div>
<div class="abs" style="left:434px;top:4068px;font-size:12px;color:var(--white)">Copyright © 2024 &nbsp;Marlow Pool Service. All Right Reserved.</div>

</body>
</html>
```